Business Cards for a law firm

Business cards for our law firm. Use our silhoette logo and OAK PARTNERS - check our website (www.oakpartners.example)

Contact Information for Business Card

our silhouette logo, OAK PARTNERS, 800-555-0147, Dorian Pemberton, dorian@oakpartners.example

Requirements
Must have
• our silhouette logo, OAK PARTNERS, 800-555-0147, Dorian Pemberton, dorian@oakpartners.example

```html
<!DOCTYPE html>
<html lang="en">
<head>
<meta charset="utf-8">
<title>Oak Partners – Business Cards</title>
<link href="https://fonts.googleapis.com/css2?family=Montserrat:wght@400;500;700&display=swap" rel="stylesheet">
<style>
  :root {
    --backdrop: #3b3d3d;
    --card: #1f1f1f;
    --accent: #e39a1f;
    --brand-blue: #1f2c66;
    --text-grey: #8a8a8a;
    --text-muted: #7a7a7a;
    --mark-dark: #0e0e0e;
  }
  * { margin: 0; padding: 0; box-sizing: border-box; }
  html, body {
    width: 1200px; height: 1168px; overflow: hidden;
    background: var(--backdrop);
    font-family: 'Montserrat', sans-serif;
  }
  .card {
    position: absolute; left: 246px; width: 701px; height: 400px;
    background: var(--card);
    border-left: 3px solid var(--accent);
    border-bottom: 3px solid var(--accent);
  }
  .card--front { top: 138px; }
  .card--back { top: 612px; }

  .brand-mark {
    position: absolute; display: flex; align-items: center; gap: 12px;
    font-weight: 700; letter-spacing: 1px; white-space: nowrap;
  }
  .brand-mark__square { display: block; }
  .card--front .brand-mark { left: 29px; top: 42px; color: var(--brand-blue); font-size: 31px; }
  .card--front .brand-mark__square { width: 30px; height: 30px; background: var(--brand-blue); }
  .card--back .brand-mark { left: 50%; top: 176px; transform: translateX(-50%); color: var(--mark-dark); font-size: 36px; }
  .card--back .brand-mark__square { width: 34px; height: 34px; background: var(--mark-dark); }

  .portrait {
    position: absolute; left: 336px; top: 88px; width: 188px; height: 286px;
    background: linear-gradient(90deg, #0c0c0c 0%, #151515 48%, #2c3131 70%, #4a5252 100%);
    border-radius: 40px 40px 4px 4px;
  }

  .identity { position: absolute; left: 29px; top: 176px; }
  .identity__firm { color: var(--brand-blue); font-weight: 700; font-size: 26px; line-height: 1; }
  .identity__practice { color: var(--text-muted); font-size: 13px; letter-spacing: 4.6px; margin-top: 8px; }
  .identity__rule { width: 22px; height: 2px; background: var(--accent); margin-top: 16px; }
  .identity__name { color: var(--text-grey); font-size: 19px; font-weight: 500; letter-spacing: 1px; margin-top: 14px; line-height: 1.1; }
  .identity__title { color: var(--text-muted); font-size: 16px; font-weight: 500; letter-spacing: 1px; line-height: 1.2; }

  .contact { position: absolute; left: 29px; top: 308px; list-style: none; }
  .contact__item {
    display: flex; align-items: center; gap: 10px;
    color: var(--text-muted); font-size: 14px; letter-spacing: 1px; height: 23px;
    white-space: nowrap;
  }
  .contact__icon { width: 18px; height: 16px; flex: none; }
</style>
</head>
<body>

<section class="card card--front">
  <div class="brand-mark">
    <span class="brand-mark__square"></span>
    <span>OAK PARTNERS</span>
  </div>

  <div class="portrait" role="img" aria-label="Silhouettes of two men in suits standing side by side"></div>

  <div class="identity">
    <p class="identity__firm">OAK PARTNERS</p>
    <p class="identity__practice">INJURY ATTORNEYS</p>
    <div class="identity__rule"></div>
    <p class="identity__name">DORIAN PEMBERTON</p>
    <p class="identity__title">ATTORNEY</p>
  </div>

  <ul class="contact">
    <li class="contact__item">
      <svg class="contact__icon" viewBox="0 0 18 16" aria-hidden="true">
        <path d="M3 1.5 L6 1 L7.5 4.5 L5.8 6 Q7.5 9.5 11 11 L12.5 9.3 L16 10.8 L15.5 13.8 Q7 14.5 3 1.5 Z" fill="none" stroke="#e39a1f" stroke-width="1.6" stroke-linejoin="round"/>
      </svg>
      <span>800-555-0147</span>
    </li>
    <li class="contact__item">
      <svg class="contact__icon" viewBox="0 0 18 16" aria-hidden="true">
        <rect x="1" y="3" width="16" height="11" fill="#e39a1f"/>
        <path d="M1 3 L9 9.5 L17 3" fill="none" stroke="#1f1f1f" stroke-width="1.4"/>
      </svg>
      <span>dorian@oakpartners.example</span>
    </li>
    <li class="contact__item">
      <svg class="contact__icon" viewBox="0 0 18 16" aria-hidden="true">
        <circle cx="9" cy="8" r="6.5" fill="none" stroke="#e39a1f" stroke-width="1.5"/>
        <ellipse cx="9" cy="8" rx="2.8" ry="6.5" fill="none" stroke="#e39a1f" stroke-width="1.2"/>
        <path d="M2.5 8 H15.5" stroke="#e39a1f" stroke-width="1.2"/>
      </svg>
      <span>www.oakpartners.example</span>
    </li>
  </ul>
</section>

<section class="card card--back">
  <div class="brand-mark">
    <span class="brand-mark__square"></span>
    <span>OAK PARTNERS</span>
  </div>
</section>

</body>
</html>
```